The most modern business card ever !!!

Our company call “Vendalo”. Vendalo is a technology company specialized in cruises solutions. Out main product is a platform to reserve cruises. This is a revolutionary platform that make easier to travel agencies and final users to reserve cruises across dozen companies like tibba, wernu, hpv, dgb, etc..We are a “start up”, with a young team of developers and we want to transmit it.. For it, we want something different, a modern business card that represent cruises and technology.. When someone receive this card, this person should say: wowww this is different… this is modern… this is a cruise related company..
- diferent, modern
- traditions business card

```html
<!DOCTYPE html>
<html lang="en">
<head>
<meta charset="utf-8">
<title>Vendalo Business Card</title>
<link href="https://fonts.googleapis.com/css2?family=Exo+2:wght@600;700&family=Open+Sans:wght@400&family=Roboto:wght@400&display=swap" rel="stylesheet">
<style>
  :root {
    --backdrop: #5c5c5c;
    --paper: #ffffff;
    --brand-blue: #29a9e1;
    --ink: #1a1a1a;
    --text-grey: #3d3d3d;
    --rule: #d6d6d6;
  }
  html, body {
    margin: 0;
    padding: 0;
    width: 1200px;
    height: 802px;
    overflow: hidden;
    background: var(--backdrop);
  }
  .canvas {
    position: relative;
    width: 1200px;
    height: 802px;
  }
  .card {
    position: absolute;
    top: 274px;
    width: 442px;
    height: 265px;
    box-shadow: 2px 3px 6px rgba(0,0,0,0.45);
  }
  .card--front { left: 136px; background: var(--paper); }
  .card--back  { left: 624px; background: var(--brand-blue); }

  .wordmark {
    position: absolute;
    font-family: "Exo 2", sans-serif;
    font-weight: 600;
    line-height: 1;
    letter-spacing: 1px;
  }
  .card--front .wordmark {
    left: 34px;
    top: 112px;
    font-size: 40px;
    color: var(--ink);
  }
  .card--back .wordmark {
    left: 0;
    right: 0;
    top: 104px;
    text-align: center;
    font-size: 56px;
    color: var(--paper);
  }

  .divider {
    position: absolute;
    left: 232px;
    top: 60px;
    width: 1px;
    height: 140px;
    background: var(--rule);
  }
  .details {
    position: absolute;
    left: 246px;
    top: 62px;
    color: var(--text-grey);
  }
  .person-name {
    margin: 0;
    font-family: "Exo 2", sans-serif;
    font-weight: 700;
    font-size: 15.5px;
    letter-spacing: 0.3px;
    color: var(--brand-blue);
    line-height: 18px;
  }
  .person-role {
    margin: 0 0 6px;
    font-family: "Roboto", sans-serif;
    font-size: 13px;
    line-height: 15px;
  }
  .contact-list {
    list-style: none;
    margin: 0 0 4px;
    padding: 0;
    font-family: "Roboto", sans-serif;
    font-size: 12.5px;
    line-height: 16px;
  }
  .contact-list li {
    display: flex;
    align-items: center;
    gap: 3px;
  }
  .contact-icon {
    width: 10px;
    height: 10px;
    fill: var(--brand-blue);
    flex: none;
  }
  .address {
    margin: 0;
    font-family: "Open Sans", sans-serif;
    font-size: 12.8px;
    line-height: 16px;
    font-style: normal;
    letter-spacing: 0.2px;
  }
</style>
</head>
<body>
<main class="canvas">
  <section class="card card--front">
    <div class="wordmark">Vendalo</div>
    <div class="divider"></div>
    <div class="details">
      <h1 class="person-name">DORIAN VELL</h1>
      <p class="person-role">Managing Director</p>
      <ul class="contact-list">
        <li>
          <svg class="contact-icon" viewBox="0 0 10 10" aria-hidden="true"><path d="M0 4 Q5 0 10 4 L8.5 5 L7 4 L7 3.2 Q5 2.6 3 3.2 L3 4 L1.5 5 Z M2.5 5.5 L7.5 5.5 L9 9 L1 9 Z"/></svg>
          044-987 654 321
        </li>
        <li>
          <svg class="contact-icon" viewBox="0 0 10 10" aria-hidden="true"><path d="M2.5 0 H7.5 V10 H2.5 Z M3.5 1.2 V7.8 H6.5 V1.2 Z" fill-rule="evenodd"/></svg>
          044-987 654 321
        </li>
        <li>
          <svg class="contact-icon" viewBox="0 0 10 10" aria-hidden="true"><path d="M0 2 H10 V8 H0 Z M0.8 2.6 L5 5.6 L9.2 2.6" fill-rule="evenodd"/><path d="M0.8 2.6 L5 5.6 L9.2 2.6" stroke="#fff" stroke-width="0.8" fill="none"/></svg>
          hello@vendalomail.com
        </li>
        <li>
          <svg class="contact-icon" viewBox="0 0 10 10" aria-hidden="true"><circle cx="5" cy="5" r="4.6"/><path d="M2.5 3.5 Q4 2.5 5 3.8 Q4.5 5.5 6.5 6.2 L5.5 8" stroke="#fff" stroke-width="0.9" fill="none"/></svg>
          www.vendalocruise.com
        </li>
      </ul>
      <address class="address">12345, Address Goes Here<br>Country Name, 123456.</address>
    </div>
  </section>

  <section class="card card--back">
    <div class="wordmark">Vendalo</div>
  </section>
</main>
</body>
</html>
```